U.S. Popcorn company needs business cards

We are a popcorn company that manufactures popcorn and sells it to grocery stores worldwide. Our theme is "Americana" and our logo is U.S. route 66 which is the most famous highway in the U.S.

We would like the design to be simple and to use both sides. On the back side we would like to see just the logo and website. The front would be normal details

Target Market(s)

Wholesalers, grocers and distributors

Industry/Entity Type

Manufacture

Contact Information for Business Card

Business name: Prairie Lantern Popcorn
Phone: +1 555 308 4726
Email: Dale@prairielanternpopcorn.com
website: www.prairielanternpopcorn.com
Tag Line: "Good corn, good times"
Name: Dale Whitcombe
Title: Founder/President

Requirements
Must have
• Either this design should be fun or clean and simple. I will let you show me your thougths.
Nice to have
• Anything that ties in the real Hwy Route 66.
• Colors might need to be red, white and blue incorporated.
Should not have
• Not be too busy.

```html
<!DOCTYPE html>
<html lang="en">
<head>
<meta charset="utf-8">
<title>Prairie Lantern Popcorn – Business Card</title>
<link href="https://fonts.googleapis.com/css2?family=Lato:wght@400;700&display=swap" rel="stylesheet">
<style>
  :root {
    --page-bg: #d9d2c7;
    --navy-deep: #0b0f30;
    --navy-mid: #1f2656;
    --paper: #f2f1ef;
    --flag-red: #c8141c;
    --text-light: #dcdde6;
    --text-soft: #c9cad6;
    --tagline: #a79a86;
  }
  * { margin: 0; padding: 0; box-sizing: border-box; }
  html, body {
    width: 1200px; height: 970px; overflow: hidden;
    background: var(--page-bg);
    font-family: "Lato", Arial, sans-serif;
  }
  .card {
    position: absolute; left: 80px; top: 189px;
    width: 1040px; height: 592px; overflow: hidden;
    background: radial-gradient(ellipse 420px 520px at 230px 330px, var(--navy-mid), var(--navy-deep) 85%);
    box-shadow: 0 10px 30px rgba(0,0,0,0.25);
  }
  .card-art { position: absolute; inset: 0; width: 1040px; height: 592px; }
  .company-name {
    position: absolute; left: 60px; top: 70px;
    font-size: 39px; font-weight: 400; color: var(--text-light);
  }
  .person { position: absolute; left: 60px; top: 220px; }
  .person-name { font-size: 38px; color: var(--text-light); line-height: 1.05; }
  .person-title { font-size: 27px; color: var(--flag-red); line-height: 1.1; }
  .address {
    position: absolute; left: 62px; top: 346px;
    font-size: 26px; color: var(--text-soft); line-height: 35px;
  }
  .contacts { position: absolute; left: 62px; top: 435px; list-style: none; }
  .contacts li {
    display: flex; align-items: center; height: 34.5px;
    font-size: 26px; color: var(--text-soft);
  }
  .contact-icon {
    width: 30px; height: 30px; margin-right: 12px;
    background: var(--flag-red); display: flex; align-items: center; justify-content: center;
  }
  .brand-mark {
    position: absolute; left: 700px; top: 100px; width: 310px;
    text-align: center; font-size: 40px; font-weight: 700;
    color: var(--navy-deep); line-height: 1.15;
  }
  .tagline {
    position: absolute; right: 62px; top: 505px;
    font-size: 26px; color: var(--tagline);
  }
</style>
</head>
<body>
  <div class="card">
    <svg class="card-art" viewBox="0 0 1040 592" role="img" aria-label="Light brand panel with a red accent band">
      <path fill="var(--flag-red)" d="M590,0 L1040,0 L1040,372 Q815,445 625,348 Q565,295 590,0 Z"/>
      <path fill="var(--paper)" d="M600,0 L1040,0 L1040,352 Q820,420 640,330 Q582,282 600,0 Z"/>
    </svg>

    <div class="company-name">Prairie Lantern Popcorn</div>

    <div class="person">
      <div class="person-name">Dale Whitcombe</div>
      <div class="person-title">Founder/President</div>
    </div>

    <div class="address">Millbrook, KS<br>United States</div>

    <ul class="contacts">
      <li>
        <span class="contact-icon">
          <svg width="20" height="20" viewBox="0 0 20 20"><path fill="#fff" d="M4 2h4l1 4-2 2c1 2 3 4 5 5l2-2 4 1v4c0 1-1 2-2 2C8 18 2 12 2 4c0-1 1-2 2-2z"/></svg>
        </span>+1 555 308 4726
      </li>
      <li>
        <span class="contact-icon">
          <svg width="20" height="16" viewBox="0 0 20 16"><rect x="1" y="1" width="18" height="14" fill="none" stroke="#fff" stroke-width="2"/><path d="M1 1l9 8 9-8" fill="none" stroke="#fff" stroke-width="2"/></svg>
        </span>Dale@prairielanternpopcorn.com
      </li>
      <li>
        <span class="contact-icon">
          <svg width="20" height="20" viewBox="0 0 20 20"><circle cx="10" cy="10" r="8" fill="none" stroke="#fff" stroke-width="2"/><path d="M2 10h16M10 2c-4 5-4 11 0 16M10 2c4 5 4 11 0 16" fill="none" stroke="#fff" stroke-width="1.5"/></svg>
        </span>www.prairielanternpopcorn.com
      </li>
    </ul>

    <div class="brand-mark">Prairie Lantern<br>Popcorn</div>

    <div class="tagline">Good corn, good times</div>
  </div>
</body>
</html>
```